Kestrel Facilities Business Card Design

We would now like to design business cards with the new Kestrel Facilities logo

Target Market(s)

Professional

Industry/Entity Type

Professional services

Contact Information for Business Card

Employee name, title, phone number, email address, corporate office address and logo.

Font styles to use
Sans Serif

Colors
0054AA
0677BA
7BADD7
CADEEF
E8F1F8

Requirements
Must have
• My logo
Should not have
• any other pictures or images besides my logo

```html
<!DOCTYPE html>
<html lang="en">
<head>
<meta charset="utf-8">
<title>Kestrel Facilities Business Card</title>
<link href="https://fonts.googleapis.com/css2?family=Josefin+Sans:wght@400;600&family=Montserrat:wght@600;700&display=swap" rel="stylesheet">
<style>
  :root {
    --brand-blue: #2f74bc;
    --brand-deep: #0054aa;
    --ink: #1c1c1c;
    --paper: #ffffff;
    --backdrop: #2b2b2b;
  }
  * { box-sizing: border-box; margin: 0; padding: 0; }
  html, body {
    width: 1200px; height: 960px; overflow: hidden;
    background: var(--backdrop);
  }
  .stage {
    position: relative; width: 1200px; height: 960px;
    display: flex; flex-direction: column; align-items: center; justify-content: center; gap: 60px;
  }
  .card {
    position: relative; width: 620px; height: 354px; border-radius: 18px;
    box-shadow: 0 10px 24px rgba(0,0,0,.45);
    overflow: hidden;
  }
  .card--back {
    background: var(--brand-blue);
    display: flex; align-items: center; justify-content: center;
  }
  .card--front { background: var(--paper); }

  .wordmark {
    display: flex; align-items: center; gap: 14px;
    font-family: "Montserrat", sans-serif; font-weight: 700;
    letter-spacing: .04em; text-transform: uppercase; line-height: 1.05;
  }
  .wordmark__square { width: 34px; height: 34px; flex: none; }
  .wordmark__name { font-size: 30px; }
  .card--back .wordmark { color: #e3e8f2; }
  .card--back .wordmark__square { background: #e3e8f2; }
  .card--front .wordmark { position: absolute; top: 42px; right: 44px; color: var(--brand-blue); }
  .card--front .wordmark__name { font-size: 24px; }
  .card--front .wordmark__square { width: 28px; height: 28px; background: var(--brand-blue); }

  .divider {
    position: absolute; left: 40px; right: 40px; top: 186px;
    height: 2px; background: var(--brand-blue);
  }
  .person { position: absolute; left: 40px; top: 122px; }
  .person__name {
    font-family: "Montserrat", sans-serif; font-weight: 700;
    font-size: 26px; color: var(--brand-blue); letter-spacing: .01em;
  }
  .person__title {
    font-family: "Josefin Sans", sans-serif; font-size: 19px; color: var(--ink); margin-top: 4px;
  }
  .address {
    position: absolute; right: 40px; top: 204px; text-align: right;
    font-family: "Josefin Sans", sans-serif; font-size: 17px; color: var(--ink); line-height: 1.35;
  }
  .contacts {
    position: absolute; left: 40px; top: 214px; list-style: none;
    font-family: "Josefin Sans", sans-serif; font-size: 18px; color: var(--ink);
  }
  .contacts li { display: flex; align-items: center; gap: 10px; height: 30px; }
  .contacts svg { width: 16px; height: 16px; fill: var(--brand-blue); flex: none; }
</style>
</head>
<body>
<main class="stage">
  <section class="card card--back" aria-label="Business card back">
    <div class="wordmark">
      <span class="wordmark__square"></span>
      <span class="wordmark__name">Kestrel<br>Facilities</span>
    </div>
  </section>

  <section class="card card--front" aria-label="Business card front">
    <div class="wordmark">
      <span class="wordmark__square"></span>
      <span class="wordmark__name">Kestrel<br>Facilities</span>
    </div>

    <div class="person">
      <h1 class="person__name">AMARA NJOKI</h1>
      <p class="person__title">Co-Founder</p>
    </div>

    <div class="divider"></div>

    <p class="address">P.O Box 4410-00200<br>Nairobi, Kenya</p>

    <ul class="contacts">
      <li>
        <svg viewBox="0 0 24 24" aria-hidden="true"><path d="M6.6 10.8a15.1 15.1 0 0 0 6.6 6.6l2.2-2.2c.3-.3.7-.4 1-.2 1.1.4 2.3.6 3.6.6.6 0 1 .4 1 1V20c0 .6-.4 1-1 1A17 17 0 0 1 3 4c0-.6.4-1 1-1h3.5c.6 0 1 .4 1 1 0 1.3.2 2.5.6 3.6.1.3 0 .7-.2 1z"/></svg>
        <span>+254-100-55012</span>
      </li>
      <li>
        <svg viewBox="0 0 24 24" aria-hidden="true"><path d="M2 5h20v14H2zm2 2v.5l8 5 8-5V7l-8 5z"/></svg>
        <span>info@kestrelfacilities.com</span>
      </li>
      <li>
        <svg viewBox="0 0 24 24" aria-hidden="true"><circle cx="12" cy="12" r="10"/><path d="M2 12h20M12 2c3 3 3 17 0 20M12 2c-3 3-3 17 0 20" stroke="#fff" stroke-width="1.4" fill="none"/></svg>
        <span>www.kestrelfacilities.com</span>
      </li>
    </ul>
  </section>
</main>
</body>
</html>
```